Branding product image: VELMOT (Golden Papaya) in Plastic Cup (Ready to Eat)

The product is sliced Fruit in Light syrup
Flavour: VELMOT (Golden Papaya)
The temporary product name: VELMOT
I want the product design to be something 'fun', 'natural', and 'colourful'
The design concept could be anything depends on your imagination, but it must be eye catchy and attractive.
Basically, I want you to be creative in designing the logo and the overall graphic design for the label.
The measurement is 20 cm (Length) x 6,5 cm (Height)
The target customers are young and health conscious audiences (10 years - 65 years old).
Create something different. Something extraordinary.
Brief summary about the fruit:
This fruit only grows in certain part of the world. It grows in mountain area that is in tropical climate. The fruit flesh has a yellowish-golden color. It has an extraordinary taste (unlike normal papaya) and it suits very well with any dishes from cold appetizer, white/ red meat, desserts, and cocktails.
I need a packaging design for Fruit Cup productThe product is sliced Fruit in Light syrup.There will be various flavours i.e. apple, lychee, peach, papaya, etc.However, you may design the product using one sample flavour (i.e. papaya) first, as the designs of other flavours could be adjusted afterwards.The temporary product name is: RICCANAI want the product design to be something 'fun', 'natural', and 'colourful'.The design concept could be anything depends on your imagination. Basically, I want you to be creative in designing the logo and the overall graphic design for the label. - Create something different. Something extraordinary -Additional:The measurement is 20cm (Length) x 5cm (Height).The target customers are young audiences (10 years - 35 years old).The product design must stand out in the supermarket shelf.It must be eye catchy and attractive.Thank you,Jordan-PLEASE REFER TO DESIGN SAMPLE ATTACHED TO HAVE A BETTER UNDERSTANDING FOR THE PRODUCT CONCEPT- Added Wednesday, September 17, 2014
Project Deadline Extended Reason: Haven't found a good design. Added Friday, September 19, 2014
Project Deadline Extended Reason: Need more time for designers to finalize and perfect the design.Thank you,Jordan Added Monday, September 29, 2014
Project Deadline Extended Reason: I haven't found a great design yet. Added Tuesday, February 24, 2015
Reason: Getting better designs now. Still Open to new ideas while refining the latest designs from some designers.
Please do your best in submitting other great designs!

```html
<!DOCTYPE html>
<html lang="en">
<head>
<meta charset="utf-8">
<title>VELMOT Sliced Fruit – Cup Label</title>
<link rel="stylesheet" href="https://fonts.googleapis.com/css2?family=Signika:wght@400;600;700&family=Arimo:wght@400;700&display=swap">
<style>
  :root {
    --stage: #e2e2e2;
    --blue-deep: #16279a;
    --blue-mid: #2a3fc9;
    --blue-light: #3a52dc;
    --orange: #f26a1b;
    --lime: #d6ec3c;
    --white: #ffffff;
    --ink: #111111;
  }
  * { box-sizing: border-box; margin: 0; padding: 0; }
  html, body { width: 1200px; height: 1000px; overflow: hidden; }
  body { background: var(--stage); font-family: "Signika", sans-serif; position: relative; }

  .lid {
    position: absolute; top: 50px; width: 220px; height: 220px; border-radius: 50%;
    background: radial-gradient(circle at 50% 40%, var(--blue-light), var(--blue-deep));
    border: 10px solid var(--white);
    display: flex; flex-direction: column; align-items: center; justify-content: center; gap: 6px;
  }
  .lid--front { left: 200px; }
  .lid--back { left: 780px; }
  .lid .brand-name { font-size: 34px; }
  .lid .product-line { font-size: 14px; }
  .lid .product-line small { font-size: 11px; }
  .lid .claim { font-size: 20px; }

  .panel {
    position: absolute; top: 310px; width: 500px; height: 620px; overflow: hidden;
    background: linear-gradient(90deg, var(--blue-deep) 0%, var(--blue-mid) 30%, var(--blue-light) 55%, var(--blue-mid) 80%, var(--blue-deep) 100%);
  }
  .panel--front { left: 60px; }
  .panel--back { left: 640px; }

  .brand-name { color: var(--orange); font-weight: 700; letter-spacing: 1px; line-height: 1; }
  .product-line {
    color: var(--white); font-weight: 600; text-align: center; line-height: 1.1; letter-spacing: 0.5px;
  }
  .product-line small { display: block; font-weight: 400; letter-spacing: 0; }

  .front-lockup {
    position: absolute; top: 44px; left: 0; width: 100%; display: flex; flex-direction: column; align-items: center; gap: 12px;
  }
  .front-lockup .brand-name { font-size: 72px; }
  .front-lockup .product-line { font-size: 30px; }
  .front-lockup .product-line small { font-size: 20px; }

  .artwork { position: absolute; left: 0; top: 0; }

  .claim { color: var(--white); font-weight: 700; line-height: 1; text-align: center; }
  .claim small { display: block; font-weight: 400; font-size: 0.42em; color: var(--lime); margin-top: 4px; }
  .front-claim { position: absolute; right: 46px; top: 270px; font-size: 38px; }

  .net-weight {
    position: absolute; left: 30px; bottom: 70px; color: var(--white);
    font-family: "Arimo", sans-serif; font-size: 16px; line-height: 1.25;
  }

  .nutrition {
    position: absolute; top: 40px; left: 30px; width: 440px; background: var(--white);
    border: 3px solid var(--ink); border-radius: 6px; padding: 12px 14px;
    display: grid; grid-template-columns: 1fr 1.25fr; gap: 14px;
    font-family: "Arimo", sans-serif; color: var(--ink); font-size: 13px; line-height: 1.3;
  }
  .nutrition h2 { font-size: 30px; line-height: 0.95; font-weight: 700; margin-bottom: 6px; }
  .nutrition .note { font-size: 11px; padding-left: 8px; margin: 4px 0; }
  .nutrition ul { list-style: none; font-weight: 700; }
  .nutrition ul li::before { content: "• "; }
  .nutrition table { width: 100%; border-collapse: collapse; font-size: 13px; }
  .nutrition th { font-weight: 400; text-align: left; border-bottom: 5px solid var(--ink); padding-bottom: 2px; }
  .nutrition th:last-child, .nutrition td:last-child { text-align: right; }
  .nutrition td { border-bottom: 1px solid var(--ink); padding: 2px 0; }
  .nutrition tr.last td { border-bottom: 4px solid var(--ink); font-weight: 700; }
  .nutrition .bold { font-weight: 700; }
  .nutrition .sub { padding-left: 14px; }

  .back-lockup {
    position: absolute; top: 380px; left: 0; width: 100%; display: flex; flex-direction: column; align-items: center; gap: 8px;
  }
  .back-lockup .brand-name { font-size: 54px; }
  .back-lockup .product-line { font-size: 22px; }
  .back-lockup .product-line small { font-size: 15px; }

  .distributor {
    position: absolute; bottom: 40px; width: 100%; text-align: center; color: var(--white);
    font-family: "Arimo", sans-serif; font-size: 12px; line-height: 1.4;
  }
  .distributor .web { font-weight: 700; }
</style>
</head>
<body>

  <div class="lid lid--front">
    <span class="brand-name">VELMOT</span>
    <div class="product-line">SLICED FRUIT<small>in Light syrup</small></div>
    <div class="claim">100%</div>
  </div>
  <div class="lid lid--back">
    <span class="brand-name">VELMOT</span>
    <div class="product-line">SLICED FRUIT<small>in Light syrup</small></div>
    <div class="claim">100%</div>
  </div>

  <section class="panel panel--front">
    <svg class="artwork" width="500" height="620" viewBox="0 0 500 620" role="img" aria-label="Illustration of a sliced golden papaya with black seeds over a white brush swoosh and lime streaks">
      <defs>
        <linearGradient id="papayaTone" x1="0" y1="0" x2="1" y2="1">
          <stop offset="0" stop-color="#ffffff"/>
          <stop offset="0.3" stop-color="#f7a23a"/>
          <stop offset="0.7" stop-color="#f26a1b"/>
          <stop offset="1" stop-color="#d6ec3c"/>
        </linearGradient>
      </defs>
      <path d="M0 270 C120 250 260 220 330 210 C300 300 330 420 320 560 C250 520 140 470 0 420 Z" fill="url(#papayaTone)"/>
    </svg>

    <div class="front-lockup">
      <span class="brand-name">VELMOT</span>
      <div class="product-line">SLICED FRUIT<small>in Light syrup</small></div>
    </div>

    <div class="claim front-claim">100%<small>fresh-natural</small></div>

    <div class="net-weight">NET WT. 1.08oz<br>122gms</div>
  </section>

  <section class="panel panel--back">
    <div class="nutrition">
      <div>
        <h2>Nutrition Facts</h2>
        <p>Serving Size 1/2 Cup (4oz.)</p>
        <p>Serving about 2</p>
        <p class="bold">Calories 85</p>
        <p class="sub">Fat Calories 0</p>
        <p class="note">*Percent Daily Values (DV) are based on a 2,000 calorie diet.</p>
        <ul>
          <li>Vitamin A 0%</li>
          <li>Vitamin C 0%</li>
          <li>Calcium 0%</li>
          <li>Iron 0%</li>
        </ul>
      </div>
      <table>
        <tr><th>Amount / serving</th><th>% DV*</th></tr>
        <tr><td class="bold">Total Fat 0g</td><td class="bold">0%</td></tr>
        <tr><td class="sub">Sat. Fat &nbsp; 0g</td><td class="bold">0%</td></tr>
        <tr><td class="sub">Trans. Fat 0g</td><td></td></tr>
        <tr><td class="bold">Cholest. &nbsp; 0mg</td><td class="bold">0%</td></tr>
        <tr><td class="bold">Sodium &nbsp; 0mg</td><td class="bold">0%</td></tr>
        <tr><td class="bold">Total Carb. 20g</td><td class="bold">7%</td></tr>
        <tr><td class="sub">Dietary Fiber &lt; 1g</td><td class="bold">3%</td></tr>
        <tr><td class="sub">Sugars &nbsp; 14g</td><td></td></tr>
        <tr class="last"><td>Protein &lt; 1g</td><td></td></tr>
      </table>
    </div>

    <div class="back-lockup">
      <span class="brand-name">VELMOT</span>
      <div class="product-line">SLICED FRUIT<small>in Light syrup</small></div>
    </div>

    <div class="distributor">
      Exclusively Distributed by:<br>
      Velmot Mfg. Ltd.<br>
      P: 002.468.13579 F: 002.468.13580<br>
      <span class="web">www.velmotltd.com</span>
    </div>
  </section>

</body>
</html>
```